Weightloss company needs Business Card

We want a business card that is clean and professional, yet portrays that we are a friendly, innovative, and versatile program designed to fit the needs of our clients.
I would like there to be 2 sides, one side having an appointment card, and the other side containing the logo and business information. There can be decorations on both sides. The logo is attached.

Target Market(s)

Men and women 40-60

Industry/Entity Type

Business

Contact Information for Business Card

Font styles to use
Sans Serif

Requirements
Must have
• The logo, space for business information
Nice to have
• The colors in the logo
Should not have
• No pictures of people or food

```html
<!DOCTYPE html>
<html lang="en">
<head>
<meta charset="utf-8">
<title>Renewpath Weightloss – Business Card</title>
<link href="https://fonts.googleapis.com/css2?family=Source+Sans+3:ital,wght@0,400;0,600;0,700;1,600&display=swap" rel="stylesheet">
<style>
  :root {
    --stage: #000000;
    --card: #ffffff;
    --brand-red: #ff0033;
    --ink: #111111;
    --on-red: #ffffff;
  }
  * { margin: 0; padding: 0; box-sizing: border-box; }
  html, body { width: 1200px; height: 900px; overflow: hidden; background: var(--stage); }
  body { position: relative; font-family: "Source Sans 3", "Myriad Pro", Arial, sans-serif; color: var(--ink); }

  .card {
    position: absolute; top: 275px; width: 477px; height: 294px;
    background: var(--card); overflow: hidden;
  }
  .card--front { left: 116px; border-radius: 0 56px 0 56px; }
  .card--back  { left: 622px; border-radius: 56px 0 56px 0; }

  /* Front */
  .brand-lockup {
    position: absolute; left: 46px; top: 56px;
    display: flex; align-items: center; gap: 10px;
  }
  .brand-lockup__dot {
    width: 14px; height: 14px; border-radius: 50%; background: var(--brand-red);
  }
  .brand-lockup__name {
    font-weight: 700; font-size: 24px; line-height: 1.05; color: var(--brand-red);
  }
  .holder { position: absolute; right: 19px; top: 33px; text-align: right; }
  .holder__name { font-size: 21px; font-weight: 600; color: var(--brand-red); line-height: 1.1; }
  .holder__title { font-size: 14px; line-height: 1.3; }
  .address { position: absolute; right: 21px; top: 157px; text-align: right; font-size: 14px; line-height: 17px; }
  .contacts { position: absolute; right: 19px; top: 217px; list-style: none; font-size: 14px; line-height: 17.5px; }
  .contacts li { display: flex; justify-content: flex-end; align-items: center; gap: 8px; }
  .contacts svg { width: 10px; height: 10px; fill: var(--brand-red); flex: none; }

  /* Back */
  .band { position: absolute; left: 0; right: 0; background: var(--brand-red); color: var(--on-red); }
  .band--top { top: 0; height: 100px; display: flex; align-items: center; justify-content: center; }
  .band--top .brand-lockup { position: static; }
  .band--top .brand-lockup__dot { background: var(--on-red); }
  .band--top .brand-lockup__name { color: var(--on-red); font-size: 22px; }
  .band--bottom { bottom: 0; height: 40px; display: flex; align-items: center; justify-content: center; font-size: 14px; font-weight: 600; }
  .appointment__heading {
    position: absolute; top: 122px; left: 0; right: 0; text-align: center;
    font-size: 17px; font-weight: 600; font-style: italic; color: var(--brand-red);
  }
  .appointment__field {
    position: absolute; left: 83px; width: 310px; font-size: 14px; font-weight: 700;
    display: flex; align-items: baseline; white-space: nowrap;
  }
  .appointment__label { color: var(--brand-red); margin-right: 3px; }
  .appointment__line { flex: 1; border-bottom: 2px dotted var(--ink); transform: translateY(-3px); }
  .appointment__unit { margin: 0 1px; }
  .field-name { top: 162px; }
  .field-date { top: 197px; }
  .field-time { top: 233px; }
</style>
</head>
<body>
  <section class="card card--front" aria-label="Business card front">
    <div class="brand-lockup">
      <span class="brand-lockup__dot"></span>
      <span class="brand-lockup__name">Renewpath<br>Weightloss</span>
    </div>
    <div class="holder">
      <p class="holder__name">Daniel Hartley</p>
      <p class="holder__title">Managing Director</p>
    </div>
    <p class="address">48 Meadow Lane<br>Brookfield, 204518</p>
    <ul class="contacts">
      <li>044-555 018 240
        <svg viewBox="0 0 24 24" aria-hidden="true"><path d="M6.6 10.8a15.1 15.1 0 0 0 6.6 6.6l2.2-2.2c.3-.3.7-.4 1-.2 1.1.4 2.3.6 3.6.6.6 0 1 .4 1 1V20c0 .6-.4 1-1 1C10.6 21 3 13.4 3 4c0-.6.4-1 1-1h3.5c.6 0 1 .4 1 1 0 1.3.2 2.5.6 3.6.1.3 0 .7-.2 1z"/></svg>
      </li>
      <li>hello@renewpath.com
        <svg viewBox="0 0 24 24" aria-hidden="true"><path d="M2 5h20v14H2z M3 6l9 7 9-7" /></svg>
      </li>
      <li>www.renewpath.com
        <svg viewBox="0 0 24 24" aria-hidden="true"><path d="M10 14a4 4 0 0 0 5.7 0l4-4a4 4 0 0 0-5.7-5.7l-1.5 1.5 1.4 1.4 1.5-1.5a2 2 0 0 1 2.9 2.9l-4 4a2 2 0 0 1-2.9 0zM14 10a4 4 0 0 0-5.7 0l-4 4a4 4 0 0 0 5.7 5.7l1.5-1.5-1.4-1.4-1.5 1.5a2 2 0 0 1-2.9-2.9l4-4a2 2 0 0 1 2.9 0z"/></svg>
      </li>
    </ul>
  </section>

  <section class="card card--back" aria-label="Appointment card">
    <header class="band band--top">
      <div class="brand-lockup">
        <span class="brand-lockup__dot"></span>
        <span class="brand-lockup__name">Renewpath<br>Weightloss</span>
      </div>
    </header>
    <h2 class="appointment__heading">Your Next Appointment is</h2>
    <div class="appointment__field field-name"><span class="appointment__label">Name:</span><span class="appointment__line"></span></div>
    <div class="appointment__field field-date"><span class="appointment__label">Date:</span><span class="appointment__line"></span></div>
    <div class="appointment__field field-time"><span class="appointment__label">Time:</span><span class="appointment__line"></span><span class="appointment__unit">AM</span><span class="appointment__line"></span><span class="appointment__unit">PM</span></div>
    <footer class="band band--bottom">If unable to keep appointment,&nbsp; kindly give 24hrs notice.</footer>
  </section>
</body>
</html>
```